IT company developing solutions for air cargo industry is looking for a new website

We are a professional IT company developing solutions for air cargo industry worldwide.

We are looking to update and completely redesign our current webpages: https://www.brisklane.cz/

What we like about our current pages are the animated graphics on the home page. These could stay, but not a must.

The design of the new pages should be very modern, clean, unique, creative, professional, and to make a statement. We are looking for animated graphics, cool and interesting interactions, cascading layers, etc.

Our company logo is yellow, gray and black. You don’t necessarily have to stick to this colour scheme, however the corporate colors should work well with the overal design of the web pages.
Dark mode pages are also an option.

The scope of the project would include creating a:

• Header
• Footer
• Landing page
• Navigation bar (8 tabs)
• Subpages (10)

In the first stage we are looking only for the header / footer / landing page with navigaton bar / Solutions page design.
As a second round, finalists might be asked to submit another section of the website to see their consistency in terms of the look and feel proposed for the Homepage and Solutions’ pages.
The winning designer will then complete the rest of the pages.

Attached you will find a brief for the first scope of the project. Please read the note section on slide nr. 3 carefully to understand, what we exactly are looking for to achieve.

Industry/Entity Type

Aviation

Number of Pages Required

1 page

Requirements
Must have
• See brief
Nice to have
• See brief
Should not have
• See brief

```html
<!DOCTYPE html>
<html lang="en">
<head>
<meta charset="utf-8">
<title>Brisk Lane – Air Cargo IT Solutions</title>
<link rel="stylesheet" href="https://fonts.googleapis.com/css2?family=Open+Sans:wght@700&family=Roboto:wght@400;500&display=swap">
<style>
:root{
  --yellow:#ffc915;
  --ink:#111111;
  --navy:#050d1f;
  --globe:#0d3f86;
  --muted:#b5b5b5;
  --grey:#5a5a5a;
  --rule:#dedede;
  --white:#ffffff;
}
*{margin:0;padding:0;box-sizing:border-box}
html,body{width:909px;height:1200px;overflow:hidden;background:var(--white)}
body{position:relative;font-family:'Roboto',sans-serif;color:var(--ink)}
.promo-bar{position:absolute;top:0;left:0;width:909px;height:30px;background:var(--yellow);
  font-size:9.3px;text-align:center;line-height:32px;color:var(--ink)}
.site-header{position:absolute;top:30px;left:0;width:909px;height:50px;background:var(--white)}
.brand{position:absolute;left:109px;top:16px;display:flex;align-items:center;gap:6px;
  font-size:15px;font-weight:500;color:#444;text-decoration:none}
.brand-square{width:14px;height:14px;background:var(--yellow)}
.main-nav{position:absolute;left:270px;top:0;height:50px;display:flex;align-items:center;gap:19px;
  font-size:10.5px;font-weight:500}
.main-nav a{color:var(--ink);text-decoration:none;display:flex;align-items:center;gap:5px}
.main-nav svg{width:7px;height:5px}
.hero{position:absolute;top:80px;left:0;width:909px;height:497px;
  background:radial-gradient(ellipse at 50% 40%,#0b1a33 0%,var(--navy) 70%);overflow:hidden;color:var(--white);text-align:center}
.hero h1{position:absolute;top:49px;left:0;width:909px;font-family:'Open Sans',sans-serif;font-weight:700;
  font-size:27px;line-height:42px}
.hero p{position:absolute;top:142px;left:120px;width:669px;font-size:11px;line-height:19.5px}
.btn{position:absolute;top:201px;left:388px;width:132px;height:36px;border-radius:18px;background:var(--yellow);
  color:var(--white);font-size:11px;font-weight:500;line-height:36px;text-decoration:none;
  box-shadow:0 0 14px rgba(255,201,21,.45)}
.globe{position:absolute;left:-60px;top:280px;width:1029px;height:700px;border-radius:50%;
  background:radial-gradient(ellipse at 50% 20%,#1f6bc2 0%,var(--globe) 35%,#07183a 75%);
  box-shadow:0 -4px 18px rgba(120,190,255,.55)}
.facts{position:absolute;top:577px;left:0;width:909px;height:582px;text-align:center}
.facts h2{position:absolute;top:50px;left:0;width:909px;font-family:'Open Sans',sans-serif;font-weight:700;font-size:27px}
.facts .lead{position:absolute;top:99px;left:0;width:909px;font-size:13px;color:var(--grey)}
.fact-row{position:absolute;left:110px;width:689px;height:140px;display:grid;grid-template-columns:201px 251px 237px}
.fact{border-left:1px solid var(--rule);position:relative}
.fact:last-child{border-right:1px solid var(--rule)}
.fact-icon{position:absolute;top:-8px;left:50%;margin-left:-34px;width:68px;height:66px;border-radius:6px;
  background:linear-gradient(135deg,#ffe07a,var(--yellow));opacity:.85}
.fact-num{position:absolute;top:72px;left:0;width:100%;font-family:'Open Sans',sans-serif;font-weight:700;
  font-size:27px;color:var(--muted)}
.fact-label{position:absolute;top:108px;left:0;width:100%;font-size:16px;line-height:24px}
.row-1{top:159px}
.row-2{top:380px}
.site-footer{position:absolute;top:1159px;left:0;width:909px;height:41px;background:var(--ink);color:var(--white);font-size:9.5px}
.site-footer .copy{position:absolute;left:109px;top:15px}
.site-footer .legal{position:absolute;right:109px;top:15px}
.site-footer a{color:var(--white)}
</style>
</head>
<body>
<div class="promo-bar">Affordable IT Solutions That Revolutionize Tomorrow’s Air Cargo Today</div>

<header class="site-header">
  <a class="brand" href="https://www.brisklane.cz/"><span>Brisk Lane</span><span class="brand-square"></span></a>
  <nav class="main-nav">
    <a href="#">Industries</a>
    <a href="#">Solutions <svg viewBox="0 0 7 5"><path d="M.5 .8 3.5 3.8 6.5 .8" fill="none" stroke="#111" stroke-width="1"/></svg></a>
    <a href="#">Operational Support</a>
    <a href="#">Case Studies</a>
    <a href="#">Testimonials</a>
    <a href="#">News</a>
    <a href="#">About Us <svg viewBox="0 0 7 5"><path d="M.5 .8 3.5 3.8 6.5 .8" fill="none" stroke="#111" stroke-width="1"/></svg></a>
  </nav>
</header>

<section class="hero">
  <h1>Seamlessly Connecting The Air Cargo Industry<br>From Manila To Tahiti</h1>
  <p>Blending decades of air cargo knowledge with end-to-end IT solutions. Whether you are an Airline, GSA, GHA, Forwarder or E-commerce Operator, our expertise can elevate your daily workflows, cutting down on expenses, time, and errors.</p>
  <a class="btn" href="#">LEARN MORE</a>
  <div class="globe" role="img" aria-label="Glowing network globe with a cargo plane flying between two map pins"></div>
</section>

<section class="facts">
  <h2>FACTS</h2>
  <p class="lead">We are not IT tech experts attempting to do cargo! We are cargo experts with programming skills!</p>
  <div class="fact-row row-1">
    <div class="fact"><div class="fact-icon" role="img" aria-label="Office building icon"></div><div class="fact-num">2014</div><div class="fact-label">Established</div></div>
    <div class="fact"><div class="fact-icon" role="img" aria-label="Team icon"></div><div class="fact-num">319</div><div class="fact-label">Employees</div></div>
    <div class="fact"><div class="fact-icon" role="img" aria-label="Data exchange gears icon"></div><div class="fact-num">11,500,000 +</div><div class="fact-label">Nr. of Annual Electronic<br>Exchanges</div></div>
  </div>
  <div class="fact-row row-2">
    <div class="fact"><div class="fact-icon" role="img" aria-label="Globe with location pins icon"></div><div class="fact-num">18</div><div class="fact-label">Countries covered</div></div>
    <div class="fact"><div class="fact-icon" role="img" aria-label="Handshake icon"></div><div class="fact-num">20+</div><div class="fact-label">Connected Clients</div></div>
    <div class="fact"><div class="fact-icon" role="img" aria-label="Calendar and clock icon"></div><div class="fact-num">350,000 +</div><div class="fact-label">Nr. of Annual AWBs</div></div>
  </div>
</section>

<footer class="site-footer">
  <div class="copy">Copyright© 2024 &nbsp;<a href="https://www.brisklane.cz/">Brisk Lane</a> &nbsp;| &nbsp;All Rights Reserved</div>
  <div class="legal">Terms and Conditions &nbsp;&nbsp;| &nbsp;&nbsp;Privacy Policy</div>
</footer>
</body>
</html>
```